Two Marketing Brochures

We need two professional A4 brochures (PDF + web version) to promote our new handyman services to Facility Managers in Queensland.
Brochure 1: Brightmoor Property Care Trade Services (see content Brightmoor Property Care.pdf). Create new cover page and contents page then design 2 content pages (left and right) I will then paste all text myself, rather than designing 19 pages.
Brochure 2: Brightmoor Property Care Minor Works & Maintenance – Quicker, Tidier, Leaner
Audience: Commercial property managers, Tarrow Gov, councils, schools, industrial clients
Style: Clean, modern, corporate, Brightmoor Property Care-branded
Content: Text is finalised and ready to go
Deliverables: A4 PDF (print-ready) + web version (compressed)
Optional: Integration of JobNest elements (e.g. “Book Now” QR or icon)

```html
<!DOCTYPE html>
<html lang="en">
<head>
<meta charset="utf-8">
<title>Brightmoor Property Care – Trade Services Catalogue</title>
<link rel="stylesheet" href="https://fonts.googleapis.com/css2?family=Poppins:wght@300;400;500;600;700&display=swap">
<style>
:root{
  --navy:#163a5c;
  --navy-deep:#0f2c49;
  --gold:#c8922a;
  --sky:#86cdee;
  --sky-soft:#bfe5f7;
  --ink:#1d2b38;
  --backdrop:#7b838b;
  --white:#ffffff;
}
*{box-sizing:border-box;margin:0;padding:0}
html,body{width:879px;height:1200px;overflow:hidden;background:var(--backdrop)}
body{font-family:'Poppins',sans-serif;color:var(--ink)}
.sheet{position:absolute;left:0;top:0;width:1652px;height:2255px;transform:scale(0.53208);transform-origin:0 0}
.page{position:absolute;width:724px;height:1024px;overflow:hidden;
  background:linear-gradient(90deg,var(--sky) 0%,#e9f6fd 18%,#fff 40%,#fff 65%,#e4f4fc 85%,var(--sky) 100%)}
.page--cover{left:87px;top:78px}
.page--contents{left:851px;top:78px}
.page--charge{left:87px;top:1150px}
.page--electrical{left:854px;top:1150px}

/* brand */
.brand{position:absolute;display:flex;align-items:center;gap:10px;color:var(--navy);font-weight:500;white-space:nowrap}
.brand__mark{background:var(--navy);flex:none}
.brand--cover{left:0;right:0;top:88px;justify-content:center;font-size:34px;gap:16px}
.brand--cover .brand__mark{width:30px;height:30px}
.brand--small{right:36px;top:80px;font-size:19px}
.brand--small .brand__mark{width:16px;height:16px}

/* cover */
.cover__curve{position:absolute;left:0;top:0;width:724px;height:1024px}
.cover__title{position:absolute;left:0;right:0;top:150px;text-align:center;font-weight:700;line-height:1}
.cover__title .line1{display:block;color:var(--gold);font-size:41px;letter-spacing:.5px}
.cover__title .line2{display:block;color:var(--navy);font-size:42px;margin-top:4px;letter-spacing:1px}
.cover__sub{position:absolute;left:0;right:0;top:243px;text-align:center;color:var(--navy);font-size:13.5px}
.cover__photo{position:absolute;left:130px;top:297px;width:464px;height:464px;border-radius:50%;
  border:10px solid var(--gold);
  background:linear-gradient(135deg,#d9dcdf 0%,#a9b4bd 35%,#c98a3a 55%,#6f7d89 75%,#e6e7e8 100%)}
.cover__tag{position:absolute;left:0;right:0;top:796px;text-align:center;color:var(--white)}
.cover__tag h2{font-size:18.5px;font-weight:600;line-height:1.1}
.cover__tag p{font-size:12px;font-weight:400}
.cover__rule{width:240px;height:1px;background:var(--gold);margin:12px auto 15px}
.cover__blurb{font-size:12px;line-height:1.3}
.badges{position:absolute;left:0;right:0;top:920px;display:flex;justify-content:center;gap:12px}
.badge{width:44px;height:44px;border-radius:50%;background:var(--white);border:3px solid #e3e6e8;display:flex;align-items:center;justify-content:center}
.badge i{width:24px;height:24px;border-radius:50%}
.badge--red i{background:#c9282e}.badge--green i{background:#3c9a3c}.badge--amber i{background:#e6b021}

/* contents */
.contents__title{position:absolute;left:163px;top:86px;font-size:19.5px;font-weight:600;color:var(--navy)}
.toc{position:absolute;left:163px;top:150px;width:396px;list-style:none}
.toc li{display:flex;justify-content:space-between;height:25.5px;align-items:flex-end;padding-bottom:3px;font-size:10.5px;color:var(--ink)}
.toc li span:first-child{width:362px;border-bottom:1px dotted #9aa6b0;padding-bottom:3px;margin-bottom:-3px}
.toc li span:last-child{width:24px}

/* content pages */
.heading{position:absolute;left:62px;top:117px;color:var(--navy);font-size:20px;font-weight:600}
.lede{position:absolute;left:63px;top:148px;color:var(--navy);font-size:11.5px}
.spec{position:absolute;left:64px;width:596px}
.spec__row{display:grid;grid-template-columns:186px 1fr;border-top:1px solid var(--gold);padding:16px 0 12px}
.spec__label{color:var(--navy);font-size:11.5px;padding-top:2px}
.spec__body{list-style:none;font-size:10.2px;line-height:1.16;color:var(--ink)}
.spec__body li{padding-left:8px;text-indent:-8px}
.spec__body li::before{content:"- "}
.section{position:absolute;left:62px;width:598px}
.section__title{color:var(--navy);font-size:22px;font-weight:400;padding-bottom:10px;border-bottom:1px solid var(--gold);letter-spacing:.3px}
.section .spec__row:first-of-type{border-top:none}
.section .spec__row{grid-template-columns:190px 1fr}
.footer{position:absolute;left:0;right:0;top:958px;height:44px;background:var(--navy);color:var(--white);font-size:11.5px;padding:17px 0 0 64px}
.corner{position:absolute;right:0;bottom:0;width:94px;height:94px;background:var(--gold);border-top-left-radius:100%}
.pageno{position:absolute;right:29px;top:973px;font-size:11.5px;color:var(--navy-deep)}
</style>
</head>
<body>
<main class="sheet">

  <!-- Cover -->
  <section class="page page--cover">
    <svg class="cover__curve" viewBox="0 0 724 1024" aria-hidden="true">
      <path d="M0 424 C180 470 300 470 380 452 C520 420 640 360 724 318 L724 1024 L0 1024 Z" fill="#12345a"/>
      <path d="M0 700 C200 650 500 760 724 690 L724 1024 L0 1024 Z" fill="#0f2c49" opacity=".6"/>
    </svg>
    <div class="brand brand--cover"><span class="brand__mark"></span>Brightmoor Property Care</div>
    <h1 class="cover__title"><span class="line1">TRADE SERVICES</span><span class="line2">CATALOGUE</span></h1>
    <p class="cover__sub">APPLIANCES, PLUMBING, ELECTRICAL, HEATING AND COOLING</p>
    <div class="cover__photo" role="img" aria-label="Collage: smiling tradesman in hard hat and tool belt, air-conditioning units, hands wiring a switchboard, and a chrome kitchen tap"></div>
    <div class="cover__tag">
      <h2>LEGENDARY SERVICE, DELIVERED DAILY</h2>
      <p>BPC is Plumbing, Electrical, Heating, and Cooling on demand.</p>
      <div class="cover__rule"></div>
      <p class="cover__blurb">With easy bookings, solid van tracking door-to-door, and<br>goodlooking reports, we’re guaranteed to get the job done.</p>
    </div>
    <div class="badges">
      <span class="badge badge--red"><i></i></span>
      <span class="badge badge--green"><i></i></span>
      <span class="badge badge--amber"><i></i></span>
    </div>
  </section>

  <!-- Contents -->
  <section class="page page--contents">
    <h2 class="contents__title">CONTENTS</h2>
    <div class="brand brand--small" style="top:88px;right:30px"><span class="brand__mark"></span>Brightmoor Property Care</div>
    <ol class="toc">
      <li><span>HOW WE CHARGE</span><span>3</span></li>
      <li><span>SERVICE POLICY</span><span>4</span></li>
      <li><span>SERVICE OVERVIEW - ELECTRICAL</span><span>5</span></li>
      <li><span>APPLIANCE INSPECTION (ELECTRICAL, GAS, WATER)</span><span>5</span></li>
      <li><span>ELECTRICAL SAFETY INSPECTION</span><span>5</span></li>
      <li><span>SMOKE ALARM COMPLIANCE INSPECTION</span><span>6</span></li>
      <li><span>THERMAL IMAGING – SWITCHBOARDS</span><span>T6</span></li>
      <li><span>LIGHT SWITCH REPLACEMENT</span><span>7</span></li>
      <li><span>POWERPOINT REPLACEMENT</span><span>7</span></li>
      <li><span>CEILING EXHAUST FAN REPLACEMENT</span><span>8</span></li>
      <li><span>DOWN LIGHT REPLACEMENT</span><span>8</span></li>
      <li><span>SERVICE OVERVIEW - PLUMBING</span><span>9</span></li>
      <li><span>GAS SAFETY INSPECTION</span><span>9</span></li>
      <li><span>FLEXI HOSE INSPECTION</span><span>9</span></li>
      <li><span>HOT WATER FAULTS</span><span>10</span></li>
      <li><span>TEMPORARY HOT WATER INSTALLATION</span><span>11</span></li>
      <li><span>MAJOR BLOCKAGE (Storm and Sewer)</span><span>11</span></li>
      <li><span>ROOF LEAK AND ASSESSMENT</span><span>12</span></li>
      <li><span>LEAK DETECTION - Minor Waste Blockages (Sink, Basin, Shower, etc.)</span><span>13</span></li>
      <li><span>SERVICE OVERVIEW – HEATING &amp; COOLING</span><span>14</span></li>
      <li><span>AC SPLIT SYSTEM INSPECTION &amp; DIAGNOSIS</span><span>14</span></li>
      <li><span>AC SPLIT SYSTEM SERVICE/INSPECTION</span><span>14</span></li>
      <li><span>AC SPLIT SYSTEM HYDRO CLEAN</span><span>15</span></li>
      <li><span>GAS ‘DUCTED’ HEATING SERVICE/INSPECTION</span><span>15</span></li>
      <li><span>TEMPORARY HEATING/COOLING</span><span>16</span></li>
      <li><span>CUSTOMER TERMS OF SERVICE</span><span>17</span></li>
      <li><span>SERVICE CHARGES</span><span>19</span></li>
      <li><span>Electrical</span><span>19</span></li>
      <li><span>Heating &amp; Cooling</span><span>19</span></li>
      <li><span>Plumbing</span><span>19</span></li>
      <li><span>Appliances</span><span>19</span></li>
    </ol>
  </section>

  <!-- How we charge -->
  <section class="page page--charge">
    <div class="brand brand--small"><span class="brand__mark"></span>Brightmoor Property Care</div>
    <h2 class="heading">HOW WE CHARGE</h2>
    <p class="lede">We have simplified charging to 3 different modes - so you always have control over your costs.</p>
    <div class="spec" style="top:226px">
      <div class="spec__row"><div class="spec__label">NORMAL HOURS SERVICE</div>
        <ul class="spec__body"><li>Service call includes first 15 minutes of labour.</li><li>Labour is then charged per 15-minute block thereafter.</li><li>Complete only requested or approved works.</li><li>All required material, sundries, and compliance will be charged as additional to service and labour.</li><li>Photos: before and after.</li><li>Removal and disposal of all rubbish related to works.</li><li>Area cleaned upon completion of work.</li></ul></div>
      <div class="spec__row"><div class="spec__label">Works Do Not Include</div>
        <ul class="spec__body"><li>Moving of any heavy/bulky furniture to access faults.</li><li>Any major remedial works/repairs or replacements without prior written direction/budget approval.</li></ul></div>
      <div class="spec__row"><div class="spec__label">Important Notes</div>
        <ul class="spec__body"><li>If further works are required (beyond the initial scope or budget) — unless requested — we will not invoice the original work order, instead, we will hold the original job open for 5 days for the property manager to seek authorisation for further works. This way, the property manager will avoid having multiple work orders and invoices for a single job.</li><li>After 5 days of no action or further approval, we will invoice the first attendance and wait on a new work order for further works.</li></ul></div>
      <div class="spec__row"><div class="spec__label">AFTER HOURS SERVICE</div>
        <ul class="spec__body"><li>Service does not include any labour.</li><li>Minimum charge of 1-hour labour.</li><li>After-hours loading (includes total trip travel up to 30km).</li><li>Labour is charged per 15-minute block after the first hour.</li><li>Qualify over the phone if the job is ‘urgent’ per the Residential Tenancies Act (list of urgent repairs).</li><li>Complete minimum works to make the site safe and habitable.</li><li>Complete minor repairs/replacements to avoid reattendance.</li></ul></div>
      <div class="spec__row"><div class="spec__label">Works Do Not Include</div>
        <ul class="spec__body"><li>Moving of any heavy/bulky furniture to access faults (area must be cleared by renters when reasonable to do so).</li><li>Any major remedial works/repairs or replacements.</li><li>Any removal of trade waste from site.</li></ul></div>
      <div class="spec__row"><div class="spec__label">Important Notes</div>
        <ul class="spec__body" style="padding-top:6px"><li>Works where excessive noise will be generated (rotary drilling, sewer cabling, etc.), the attending technician will at their discretion decide if this is suitable given the time of day &amp; impact of noise pollution to neighbours (e.g., cabling a sewer after 5 pm).</li><li>Works will only be attempted where the work area is deemed safe.</li><li>Where temporary services (e.g., hot water units) are installed, all trade waste related to the faulty/decommissioned unit will remain on-site and only removed once permanent replacement is approved in writing (temporary services only installed where suitable).</li></ul></div>
    </div>
    <div class="corner"></div>
    <footer class="footer">Brightmoor Property Care Pty Ltd 2025</footer>
    <span class="pageno">Pg 3</span>
  </section>

  <!-- Electrical overview -->
  <section class="page page--electrical">
    <div class="brand brand--small"><span class="brand__mark"></span>Brightmoor Property Care</div>
    <h2 class="heading">SERVICE OVERVIEW - ELECTRICAL</h2>
    <div class="section" style="top:180px">
      <h3 class="section__title">APPLIANCE INSPECTION (ELECTRICAL, GAS, WATER)</h3>
      <div class="spec__row"><div class="spec__label">WORKS INCLUDE</div>
        <ul class="spec__body"><li>Testing and diagnosis of appliance issue.</li><li>Minor repairs where economical to do so.</li><li>Report detailing the appliance issue or repairs made.</li><li>Quotation for replacement of appliance if beyond reasonable and practical repair.</li><li>Photos: before and after.</li><li>Removal and disposal of all rubbish related to works.</li><li>Area cleaned upon completion of work.</li></ul></div>
      <div class="spec__row" style="border-top:1px solid var(--gold)"><div class="spec__label">IMPORTANT NOTES</div>
        <ul class="spec__body"><li>To test and work on appliances, all appliances must be readily accessible. If we must wait an extended time for an appliance to become accessible to test (e.g., someone is using the appliance, or an oven is too hot to work on), additional hourly charges will be incurred.</li><li>All appliances/equipment must be reasonably accessible and in a clean environment. Example: Technicians cannot move dirty/clean dishes or laundry to access an appliance. Technicians require clear access to an appliance and a clean working area.</li><li>No responsibility is taken for goods damaged while working (glasses, crockery, towel, etc.) if they are not moved in preparation for the technician to complete their work.</li></ul></div>
    </div>
    <div class="section" style="top:525px">
      <h3 class="section__title">ELECTRICAL SAFETY INSPECTION</h3>
      <div class="spec__row"><div class="spec__label">WORKS INCLUDE</div>
        <ul class="spec__body"><li>Testing of all accessible parts of the electrical installation, including:</li><li>Visual inspection.</li><li>Mandatory testing in accordance with AS/NZS:3019:2022.</li><li>Audit report showing compliance and/or defect list.</li><li>Photos: before and after.</li><li>Removal and disposal of all rubbish related to works.</li><li>Area cleaned upon completion of work.</li></ul></div>
      <div class="spec__row" style="border-top:1px solid var(--gold)"><div class="spec__label">IMPORTANT NOTES</div>
        <ul class="spec__body"><li>If any part of the electrical installation is found to present clear and immediate danger to property or persons, then we will disconnect that appliance or part of the installation from supply and quote for remedial works later.</li><li>All parts of the installation and equipment must be reasonably accessible and in a clean environment. Example: Technicians cannot crawl under renters’ tables or around/over furniture to access light fixtures, power outlets, smoke alarms, nor can we be expected to move dirty dishes/glasses/appliances, etc., to access appliances.</li><li>Power must be connected to the property.</li></ul></div>
    </div>
    <div class="corner"></div>
    <footer class="footer">Brightmoor Property Care Pty Ltd 2025</footer>
    <span class="pageno">Pg 4</span>
  </section>

</main>
</body>
</html>
```